Website for Excavator and Earthworks Company

We require a modern, sleek and practical website for our newly created earthworks/excavator business in Perth, Western Australia called Bluegum Ridge Earthworks.

The website should have a modern, cutting edge feel but only needs to be relatively simplistic in it's layout and eventual functionality.

Some pages it should have would be Home, About, Projects and Contact Us.

```html
<!DOCTYPE html>
<html lang="en">
<head>
<meta charset="utf-8">
<title>Bluegum Ridge Earthworks</title>
<link rel="stylesheet" href="https://fonts.googleapis.com/css2?family=Krona+One&family=Montserrat:wght@400;500;600;700;800&display=swap">
<style>
:root{
  --lime:#c3d82c;
  --ink:#0b0b0b;
  --text:#222;
  --muted:#444;
  --pale:#f5f5f5;
  --line:#d9d9d9;
  --white:#fff;
  --footer:#000;
  --footer-bar:#151515;
}
*{box-sizing:border-box;margin:0;padding:0}
html,body{width:1200px;height:3567px;overflow:hidden}
body{font-family:"Montserrat",sans-serif;color:var(--text);background:var(--white);position:relative}
.display{font-family:"Krona One",sans-serif;text-transform:uppercase;color:var(--ink);letter-spacing:.5px}
.abs{position:absolute}
.arrow{display:inline-block;vertical-align:middle;margin-left:8px}
.eyebrow{font-family:"Krona One",sans-serif;color:var(--lime);font-size:17px;text-transform:uppercase;display:flex;align-items:center;gap:14px}
.eyebrow .rule{width:64px;height:1.5px;background:var(--lime)}
.btn{position:absolute;display:flex;align-items:center;justify-content:center;font-size:14.5px;font-weight:500;text-transform:uppercase;letter-spacing:.2px}
.btn-lime{background:var(--lime);color:var(--ink)}
.btn-dark{background:var(--ink);color:var(--white)}
.btn-light{background:var(--white);color:var(--ink)}

/* header */
.topbar{position:absolute;left:390px;top:0;width:810px;height:31px;background:var(--lime);clip-path:polygon(0 0,100% 0,100% 100%,26px 100%)}
.topbar-info{position:absolute;top:8px;font-size:13px;color:var(--ink);display:flex;align-items:center;gap:8px}
.topbar-info b{font-weight:600}
.logo{position:absolute;left:141px;top:18px;display:flex;align-items:center;gap:8px}
.logo-mark{width:22px;height:22px;background:var(--lime)}
.logo-name{font-weight:800;font-size:14px;line-height:17px;color:var(--ink);text-transform:uppercase}
.nav{position:absolute;top:54px;font-size:13.5px;font-weight:500;color:var(--ink);text-transform:uppercase}
.header-line{position:absolute;left:0;top:91px;width:1200px;height:1px;background:#e5e5e5}

/* hero */
.hero{position:absolute;left:0;top:92px;width:1200px;height:578px}
.hero-photo{position:absolute;inset:0;background:linear-gradient(90deg,#e9e8e5 0%,#e2e0dc 40%,#c9bda6 60%,#b7a27c 72%,#9b8c73 88%,#7d6f5f 100%)}
.hero-tag{position:absolute;left:141px;top:107px;height:38px;padding:0 18px;background:var(--white);font-size:13px;font-weight:600;display:flex;align-items:center;color:var(--ink)}
.hero-title{position:absolute;left:141px;top:163px;font-size:44px;line-height:57px}
.hero-lead{position:absolute;left:141px;top:282px;width:430px;padding-left:14px;border-left:4px solid var(--lime);font-size:16.5px;line-height:26px;font-weight:500;color:var(--ink)}

/* section headings */
.center-head{position:absolute;left:0;width:1200px;display:flex;flex-direction:column;align-items:center}
.section-title{font-size:29px;margin-top:12px}
.section-sub{font-size:13.5px;color:var(--ink);margin-top:20px}

/* services */
.card{position:absolute;top:880px;width:283px;height:355px;background:var(--white);box-shadow:0 4px 18px rgba(0,0,0,.07);text-align:center}
.card-photo{height:176px}
.card-title{font-size:17px;font-weight:600;color:var(--ink);margin-top:24px;text-transform:uppercase}
.card-text{font-size:13px;line-height:22px;color:var(--muted);margin:10px 24px 0}
.card-rule{height:1px;background:var(--line);margin:16px 20px 0}
.card-link{font-size:14px;font-weight:500;color:var(--ink);margin-top:14px;text-transform:uppercase}

/* about */
.about{position:absolute;left:0;top:1405px;width:1200px;height:536px;background:var(--pale)}
.about-photo{position:absolute;left:137px;top:84px;width:420px;height:367px;background:linear-gradient(180deg,#b9c0c7 0%,#c9ccd0 40%,#8a8e6e 70%,#6f6650 100%)}
.about-body{position:absolute;left:597px;top:106px;width:470px}
.about-title{font-size:29px;margin-top:14px}
.about-lead{font-size:14.5px;line-height:24px;color:var(--ink);font-weight:500;margin-top:18px}
.about-text{font-size:12.8px;line-height:24.5px;color:var(--muted);margin-top:18px}
.text-link{font-size:14px;font-weight:500;text-transform:uppercase;color:var(--ink);margin-top:26px}

/* projects */
.project{position:absolute;top:2113px;height:326px}

/* contact */
.contact{position:absolute;left:0;top:2609px;width:1200px;height:556px;background:var(--pale)}
.field{position:absolute;background:var(--white);font-size:12.5px;color:#333;padding:15px 14px}
.contact-body{position:absolute;left:637px;top:84px;width:430px}
.contact-title{font-size:29px;margin-top:14px}
.contact-text{font-size:13px;line-height:24.5px;color:var(--ink);margin-top:16px}
.contact-item{position:absolute;left:637px;display:flex;align-items:center;gap:16px;font-size:17px;color:var(--ink)}
.contact-item b{font-weight:600}
.icon-circle{width:46px;height:46px;border-radius:50%;display:flex;align-items:center;justify-content:center;background:#e8e8e8}
.icon-circle.lime{background:var(--lime)}

/* footer */
.footer{position:absolute;left:0;top:3165px;width:1200px;height:354px;background:var(--footer);color:var(--white)}
.footer-logo{position:absolute;left:141px;top:88px;display:flex;align-items:center;gap:10px}
.footer-logo .logo-name{color:var(--white);font-size:17px;line-height:21px}
.footer-about{position:absolute;left:141px;top:180px;width:260px;font-size:14.5px;line-height:24px}
.follow{position:absolute;left:141px;top:280px;display:flex;align-items:center;gap:8px;font-size:13px}
.social{width:26px;height:26px;border-radius:50%;background:#1e1e1e}
.social.lime{background:var(--lime)}
.col-rule{position:absolute;top:78px;width:1px;height:234px;background:#3a3a3a}
.col-head{position:absolute;top:89px;font-size:16px;font-weight:600}
.col-head::after{content:"";display:block;width:40px;height:2px;background:var(--lime);margin-top:7px}
.col-list{position:absolute;top:136px;list-style:none;font-size:13.5px;line-height:29px}
.foot-contact{position:absolute;left:857px;display:flex;align-items:center;gap:14px;font-size:13.5px}
.foot-icon{width:32px;height:32px;border-radius:50%;background:#1e1e1e;display:flex;align-items:center;justify-content:center}
.foot-icon.lime{background:var(--lime)}
.bottom-bar{position:absolute;left:0;top:3519px;width:1200px;height:48px;background:var(--footer-bar);color:#bbb;font-size:13px}
</style>
</head>
<body>

<!-- header -->
<div class="topbar"></div>
<div class="topbar-info" style="left:460px">
  <svg width="18" height="18" viewBox="0 0 24 24"><path d="M6.6 10.8a15 15 0 0 0 6.6 6.6l2.2-2.2a1 1 0 0 1 1-.25 11.4 11.4 0 0 0 3.6.57 1 1 0 0 1 1 1V20a1 1 0 0 1-1 1A17 17 0 0 1 3 4a1 1 0 0 1 1-1h3.5a1 1 0 0 1 1 1c0 1.25.2 2.45.57 3.57a1 1 0 0 1-.25 1z" fill="#0b0b0b"/></svg>
  <span style="margin-left:6px">Phone: <b>(08) 5550 1234 / (08) 5550 5678</b></span>
</div>
<div class="topbar-info" style="left:758px">
  <svg width="18" height="14" viewBox="0 0 18 14"><rect x="0" y="0" width="18" height="14" fill="#0b0b0b"/><path d="M1 1l8 6 8-6" stroke="#c3d82c" stroke-width="1.4" fill="none"/></svg>
  <span style="margin-left:6px">Email Us On: <b>info@bluegumridge.com.au</b></span>
</div>
<div class="logo">
  <span class="logo-mark"></span>
  <span class="logo-name">Bluegum Ridge<br>Earthworks</span>
</div>
<span class="nav" style="left:526px">Home</span>
<span class="nav" style="left:602px">About Us</span>
<span class="nav" style="left:705px">Services</span>
<span class="nav" style="left:804px">Our Project</span>
<span class="btn btn-dark" style="left:922px;top:44px;width:137px;height:36px;font-size:13px">Contact Us
  <svg class="arrow" width="14" height="10" viewBox="0 0 14 10"><path d="M0 5h12M8 1l4 4-4 4" stroke="#fff" stroke-width="1.6" fill="none"/></svg></span>
<div class="header-line"></div>

<!-- hero -->
<section class="hero">
  <div class="hero-photo" role="img" aria-label="Yellow excavator loading soil into a dump truck beside stacked steel pipes on a dusty site"></div>
  <div class="hero-tag">PERTH, WESTERN AUSTRALIA</div>
  <h1 class="hero-title display">Earth Moved<br>With Precision</h1>
  <p class="hero-lead">Professional excavation, bulk earthworks, site preparation and land development services across Perth and Western Australia.</p>
  <span class="btn btn-lime" style="left:141px;top:399px;width:184px;height:46px">View Projects
    <svg class="arrow" width="15" height="10" viewBox="0 0 15 10"><path d="M0 5h13M9 1l4 4-4 4" stroke="#0b0b0b" stroke-width="1.6" fill="none"/></svg></span>
  <span class="btn btn-light" style="left:340px;top:399px;width:168px;height:46px">Get A Quote
    <svg class="arrow" width="15" height="10" viewBox="0 0 15 10"><path d="M0 5h13M9 1l4 4-4 4" stroke="#0b0b0b" stroke-width="1.6" fill="none"/></svg></span>
</section>

<!-- services -->
<div class="center-head" style="top:751px">
  <div class="eyebrow"><span class="rule"></span>Our Services<span class="rule"></span></div>
  <h2 class="section-title display">Groundwork For Perth Future</h2>
  <p class="section-sub">Comprehensive earthmoving and excavation solutions for projects of all sizes across Perth and regional WA.</p>
</div>

<article class="card" style="left:141px">
  <div class="card-photo" role="img" aria-label="Surveyor in hi-vis vest on a cleared site with an excavator behind" style="background:linear-gradient(180deg,#c9d2db 0%,#d8c8a8 55%,#b99a6c 100%)"></div>
  <h3 class="card-title">Site Preparation</h3>
  <p class="card-text">Complete site clearing, leveling, and preparation for residential and commercial construction projects.</p>
  <div class="card-rule"></div>
  <p class="card-link">Read More <svg class="arrow" width="18" height="10" viewBox="0 0 18 10"><path d="M0 5h16M12 1l4 4-4 4" stroke="#c3d82c" stroke-width="1.8" fill="none"/></svg></p>
</article>
<article class="card" style="left:458px">
  <div class="card-photo" role="img" aria-label="Yellow backhoe loader working in a quarry cut" style="background:linear-gradient(180deg,#b5a78e 0%,#a08a66 50%,#7a6a52 100%)"></div>
  <h3 class="card-title">Excavation</h3>
  <p class="card-text">Complete site clearing, leveling, and preparation for residential and commercial construction projects.</p>
  <div class="card-rule"></div>
  <p class="card-link">Read More <svg class="arrow" width="18" height="10" viewBox="0 0 18 10"><path d="M0 5h16M12 1l4 4-4 4" stroke="#c3d82c" stroke-width="1.8" fill="none"/></svg></p>
</article>
<article class="card" style="left:776px">
  <div class="card-photo" role="img" aria-label="Mini excavator grading a long trench through farmland" style="background:linear-gradient(180deg,#c9d6dc 0%,#7f8f5e 35%,#9a7657 65%,#7e5c42 100%)"></div>
  <h3 class="card-title">Land Grading</h3>
  <p class="card-text">Complete site clearing, leveling, and preparation for residential and commercial construction projects.</p>
  <div class="card-rule"></div>
  <p class="card-link">Read More <svg class="arrow" width="18" height="10" viewBox="0 0 18 10"><path d="M0 5h16M12 1l4 4-4 4" stroke="#c3d82c" stroke-width="1.8" fill="none"/></svg></p>
</article>

<span class="btn btn-dark" style="left:479px;top:1275px;width:241px;height:46px">View More Services
  <svg class="arrow" width="15" height="10" viewBox="0 0 15 10"><path d="M0 5h13M9 1l4 4-4 4" stroke="#fff" stroke-width="1.6" fill="none"/></svg></span>

<!-- about -->
<section class="about">
  <div class="about-photo" role="img" aria-label="Orange excavator with auger attachment drilling in an open grassy field under a cloudy sky"></div>
  <div class="about-body">
    <div class="eyebrow">About Us<span class="rule"></span></div>
    <h2 class="about-title display">Built On Solid Ground</h2>
    <p class="about-lead">Bluegum Ridge Earthworks is Perth's trusted partner for excavation and earthmoving solutions Founded on principles.</p>
    <p class="about-text">Reliability, and uncompromising quality, we've built our reputation one project at a time. Our team brings decades of combined experience to every job, from residential site preparation to large-scale commercial developments. We invest in the latest equipment and technology to ensure efficiency, safety, and superior results.</p>
    <p class="text-link">View Projects <svg class="arrow" width="18" height="10" viewBox="0 0 18 10"><path d="M0 5h16M12 1l4 4-4 4" stroke="#c3d82c" stroke-width="1.8" fill="none"/></svg></p>
  </div>
</section>

<!-- projects -->
<div class="center-head" style="top:2023px">
  <div class="eyebrow"><span class="rule"></span>Selected Projects<span class="rule"></span></div>
  <h2 class="section-title display">Reliable Earthworks Across Perth</h2>
</div>
<div class="project" role="img" aria-label="Yellow excavator demolishing a brick house among rubble" style="left:141px;width:353px;background:linear-gradient(180deg,#a9b0b2 0%,#8f8a7c 45%,#6e6255 100%)"></div>
<div class="project" role="img" aria-label="Worker in hi-vis jacket watching an excavator break up a road" style="left:520px;width:230px;background:linear-gradient(180deg,#7a6f63 0%,#5d564e 50%,#8d8a84 100%)"></div>
<div class="project" role="img" aria-label="Yellow excavator digging a sand mound beside pine trees under a blue sky" style="left:776px;width:283px;background:linear-gradient(180deg,#5d9ed8 0%,#8db8d8 35%,#3e6a3a 55%,#c9935e 80%,#b17b4a 100%)"></div>
<span class="btn btn-lime" style="left:479px;top:2477px;width:241px;height:46px">View More Projects
  <svg class="arrow" width="15" height="10" viewBox="0 0 15 10"><path d="M0 5h13M9 1l4 4-4 4" stroke="#0b0b0b" stroke-width="1.6" fill="none"/></svg></span>

<!-- contact -->
<section class="contact">
  <div class="field" style="left:141px;top:84px;width:216px;height:45px">Name</div>
  <div class="field" style="left:372px;top:84px;width:216px;height:45px">Email</div>
  <div class="field" style="left:141px;top:144px;width:216px;height:45px">Phone</div>
  <div class="field" style="left:372px;top:144px;width:216px;height:45px">Subject</div>
  <div class="field" style="left:141px;top:203px;width:447px;height:45px">Your Address</div>
  <div class="field" style="left:141px;top:263px;width:447px;height:131px">How can we help solve your separation anxiety?</div>
  <span class="btn btn-lime" style="left:141px;top:427px;width:179px;height:46px">Submit Now
    <svg class="arrow" width="15" height="10" viewBox="0 0 15 10"><path d="M0 5h13M9 1l4 4-4 4" stroke="#0b0b0b" stroke-width="1.6" fill="none"/></svg></span>

  <div class="contact-body">
    <div class="eyebrow">Contact Us<span class="rule"></span></div>
    <h2 class="contact-title display">Get In To Touch</h2>
    <p class="contact-text">Comprehensive earthmoving and excavation solutions for projects of all sizes across Perth and regional WA. Perth's trusted excavation and earthworks specialists.</p>
  </div>
  <div class="contact-item" style="top:288px">
    <span class="icon-circle"><svg width="22" height="22" viewBox="0 0 24 24"><path d="M6.6 10.8a15 15 0 0 0 6.6 6.6l2.2-2.2a1 1 0 0 1 1-.25 11.4 11.4 0 0 0 3.6.57 1 1 0 0 1 1 1V20a1 1 0 0 1-1 1A17 17 0 0 1 3 4a1 1 0 0 1 1-1h3.5a1 1 0 0 1 1 1c0 1.25.2 2.45.57 3.57a1 1 0 0 1-.25 1z" fill="none" stroke="#666" stroke-width="1.3"/></svg></span>
    <span>Phone: <b>(08) 5550-1234</b></span>
  </div>
  <div class="contact-item" style="top:357px">
    <span class="icon-circle lime"><svg width="24" height="18" viewBox="0 0 24 18"><rect x="1" y="1" width="22" height="16" fill="none" stroke="#0b0b0b" stroke-width="1.4"/><path d="M1 1l11 9 11-9M1 17l8-7M23 17l-8-7" stroke="#0b0b0b" stroke-width="1.4" fill="none"/></svg></span>
    <span>Email: <b>hello@bluegumridge.com.au</b></span>
  </div>
  <div class="contact-item" style="top:425px">
    <span class="icon-circle"><svg width="18" height="24" viewBox="0 0 18 24"><path d="M9 1a8 8 0 0 1 8 8c0 6-8 14-8 14S1 15 1 9a8 8 0 0 1 8-8z" fill="none" stroke="#666" stroke-width="1.3"/><circle cx="9" cy="9" r="3" fill="none" stroke="#666" stroke-width="1.3"/></svg></span>
    <span>Location: <b>Perth, Western AUS</b></span>
  </div>
</section>

<!-- footer -->
<footer class="footer">
  <div class="footer-logo">
    <span class="logo-mark" style="width:26px;height:26px"></span>
    <span class="logo-name">Bluegum Ridge<br>Earthworks</span>
  </div>
  <p class="footer-about">Expert land solutions designed to prepare your property for development, construction At.</p>
  <div class="follow">Follow Us: <span class="social" style="margin-left:4px"></span><span class="social lime"></span><span class="social"></span></div>

  <div class="col-rule" style="left:450px"></div>
  <div class="col-rule" style="left:627px"></div>
  <div class="col-rule" style="left:828px"></div>

  <h4 class="col-head" style="left:477px">Quick Link</h4>
  <ul class="col-list" style="left:477px">
    <li>Home</li><li>About Us</li><li>Services</li><li>Our Project</li><li>Contact Us</li><li>Approach</li>
  </ul>
  <h4 class="col-head" style="left:656px">Services</h4>
  <ul class="col-list" style="left:656px">
    <li>Site Preparation</li><li>Excavation</li><li>Land Grading</li><li>Bulk Haulage</li><li>Trenching</li><li>Demolition</li>
  </ul>
  <h4 class="col-head" style="left:857px">Contact Us</h4>
  <div class="foot-contact" style="top:132px">
    <span class="foot-icon"><svg width="12" height="16" viewBox="0 0 18 24"><path d="M9 1a8 8 0 0 1 8 8c0 6-8 14-8 14S1 15 1 9a8 8 0 0 1 8-8z" fill="#fff"/><circle cx="9" cy="9" r="3" fill="#1e1e1e"/></svg></span>
    Perth, Western AUS
  </div>
  <div class="foot-contact" style="top:186px">
    <span class="foot-icon lime"><svg width="15" height="15" viewBox="0 0 24 24"><path d="M6.6 10.8a15 15 0 0 0 6.6 6.6l2.2-2.2a1 1 0 0 1 1-.25 11.4 11.4 0 0 0 3.6.57 1 1 0 0 1 1 1V20a1 1 0 0 1-1 1A17 17 0 0 1 3 4a1 1 0 0 1 1-1h3.5a1 1 0 0 1 1 1c0 1.25.2 2.45.57 3.57a1 1 0 0 1-.25 1z" fill="#0b0b0b"/></svg></span>
    Phone: (08) 5550-1234
  </div>
  <div class="foot-contact" style="top:239px">
    <span class="foot-icon"><svg width="14" height="10" viewBox="0 0 18 14"><rect width="18" height="14" fill="#fff"/><path d="M1 1l8 6 8-6" stroke="#1e1e1e" stroke-width="1.4" fill="none"/></svg></span>
    hello@bluegumridge.com.au
  </div>
</footer>
<div class="bottom-bar">
  <span class="abs" style="left:141px;top:16px">© 2023 Bluegum Ridge Earthworks. All rights reserved.</span>
  <span class="abs" style="right:141px;top:16px">privacy and policy &nbsp;|&nbsp; Terms and Conditions</span>
</div>

</body>
</html>
```